Birch And Harbor Website A Website design for book editing

A website design for book editing

Our proofreading, editing and manuscript review packages are specifically tailored to help you publish the best possible version of your story.

NEED HELP PUBLISHING A BESTSELLER?

If you’re looking for professional book editing services from senior publishing industry insiders, look no further. Besides editing, we can also answer all your publishing questions and get you started building your author platform.

OUR SERVICES

We've carefully structured our packages to maximize value for every budget.

PRICING

$.02
PER WORD
Proofreading
Line Edit (Copy-editing)
Fix spelling and grammar
Sales copy/summary revision

$.04
PER WORD
Proofreading
Line Edit (Copy-editing)
Fix spelling and grammar
Organization and content
Plot and pacing
Manuscript Review

$.06
PER WORD
Proofreading
Line Edit (Copy-editing)
Fix spelling and grammar
Organization and content
Plot and pacing
Manuscript Review
Formatting (print and ebook)
Pre-publication proofread

OUR PROCESS

Send us a sample of your book. Our caffeine-fueled, eagle-eyed editors will go through it and then email you with their comments and suggestions. You can ask them any questions you want. They will look for…

Typos and grammatical errors.
Spelling and word choice issues
Punctuation and style
Word choice, clarity and flow.
Sentence structure and craft
If your writing is already clean, then they’ll discuss bigger picture things with you, like theme, concept, purpose, audience, potential market and branding (including title, subtitle, and tagline or elevator pitch).

Once you feel comfortable and confident in an editor’s expertise, skill and knowledge, and are ready to move ahead, we’ll send an invoice for the first half of the total word count so the editor can get started. We’ll charge the rest when the project is close to completion.

Target Market(s)

Authors

Industry/Entity Type

Book Publisher

Coding

Coded - Design and coding required

Number of Pages Required

1 page

Requirements
Must have
• OUR SERVICES
• We've carefully structured our packages to maximize value for every budget.
• PRICING
• $.02
• PER WORD
• Proofreading
• Line Edit (Copy-editing)
• Fix spelling and grammar
• Sales copy/summary revision
• $.04
• PER WORD
• Proofreading
• Organization and content
• Plot and pacing
• Manuscript Review
• $.06
• PER WORD
• Proofreading
• Plot and pacing
• Manuscript Review
• Formatting (print and ebook)
• Pre-publication proofread

```html
<!DOCTYPE html>
<html lang="en">
<head>
<meta charset="utf-8">
<title>Birch And Harbor — Book Editing Services</title>
<link href="https://fonts.googleapis.com/css2?family=Raleway:wght@400;500;600;700&family=Lato:wght@400;700&display=swap" rel="stylesheet">
<style>
:root{
  --red:#e00000;
  --red-dark:#c40000;
  --ink:#222222;
  --muted:#555555;
  --white:#ffffff;
  --dark:#161616;
  --grey-band:#2a2a2a;
  --line:#e3e3e3;
}
*{box-sizing:border-box;margin:0;padding:0}
html,body{width:1200px;height:3509px;overflow:hidden}
body{position:relative;background:var(--white);font-family:'Lato',sans-serif;color:var(--ink)}
.abs{position:absolute}
.btn{position:absolute;display:flex;align-items:center;justify-content:center;background:var(--red);color:var(--white);font-family:'Lato',sans-serif;font-weight:700;border-radius:30px;text-decoration:none}
.heading{font-family:'Raleway',sans-serif}

/* header */
.site-header{position:absolute;left:0;top:0;width:1200px;height:105px;background:var(--white)}
.brand{left:98px;top:46px;font-family:'Raleway',sans-serif;font-weight:700;font-size:28px;color:var(--red);display:flex;align-items:center;gap:10px}
.brand-dot{width:14px;height:14px;border-radius:50%;background:var(--red)}
.watch{left:829px;top:24px;font-size:16px;font-weight:700;color:var(--ink);text-decoration:underline}
.btn-register{left:952px;top:16px;width:148px;height:42px;font-size:15px}
.main-nav{right:99px;top:72px;display:flex;gap:34px;font-size:15px;font-family:'Raleway',sans-serif;font-weight:500}
.main-nav a{color:var(--ink);text-decoration:none}
.main-nav a.active{color:var(--red)}

/* hero */
.hero{left:0;top:105px;width:1200px;height:452px;background:linear-gradient(100deg,#d9d9d9 0%,#8d8d8d 40%,#3c3c3c 70%,#2a2a2a 100%)}
.hero-title{left:489px;top:88px;font-family:'Raleway',sans-serif;font-weight:700;font-size:40px;line-height:46px;color:var(--white);text-transform:uppercase}
.hero-text{left:489px;top:194px;width:620px;font-size:19px;line-height:28px;font-weight:700;color:var(--white)}
.btn-hero{left:489px;top:293px;width:213px;height:51px;font-size:18px}
.scroll-down{left:571px;top:425px;width:56px;height:56px;border-radius:50%;background:var(--white);display:flex;align-items:center;justify-content:center}

/* about */
.about-kicker{left:98px;top:670px;font-family:'Raleway',sans-serif;font-size:18px;color:var(--muted)}
.about-title{left:98px;top:698px;font-family:'Raleway',sans-serif;font-weight:700;font-size:33px;color:var(--ink)}
.rule{height:3px;width:78px;background:var(--red)}
.about-rule{left:98px;top:748px}
.about-text{left:98px;top:766px;width:520px;font-size:12.5px;line-height:23px;color:var(--ink)}
.about-text p+p{margin-top:14px}
.btn-about{left:98px;top:917px;width:129px;height:47px;font-size:15px}
.about-photo{left:639px;top:676px;width:460px;height:290px;border:2px solid #cfcfcf;background:linear-gradient(135deg,#f0f0f0,#9a9a9a 55%,#4a4a4a)}

/* editing band */
.edit-band{left:0;top:1064px;width:1200px;height:367px;background:linear-gradient(90deg,var(--red-dark),var(--red) 45%,#b80000);text-align:center;color:var(--white)}
.edit-kicker{position:absolute;left:0;width:1200px;top:68px;font-family:'Raleway',sans-serif;font-size:19px}
.edit-title{position:absolute;left:0;width:1200px;top:96px;font-family:'Raleway',sans-serif;font-weight:700;font-size:31px}
.edit-text{position:absolute;left:210px;width:780px;top:165px;font-size:14px;line-height:26px}
.btn-outline{left:536px;top:253px;width:128px;height:47px;border:2px solid var(--white);background:transparent;font-size:15px}

/* services */
.service{width:318px;height:234px;top:1527px;border:2px solid #d0d0d0;background:linear-gradient(135deg,#cfcfcf,#6e6e6e 60%,#3d3d3d);color:var(--white);text-align:center}
.service h3{margin-top:62px;font-family:'Raleway',sans-serif;font-weight:700;font-size:20px}
.service p{margin:8px auto 0;width:230px;font-size:12px;line-height:19px}
.service .btn{left:103px;top:156px;width:112px;height:38px;font-size:13px}

/* process */
.process{left:0;top:1860px;width:1200px;height:456px;background:linear-gradient(180deg,#1e1e1e,#111 60%,#1c1c1c);color:var(--white);text-align:center}
.process-kicker{position:absolute;left:0;width:1200px;top:76px;font-family:'Raleway',sans-serif;font-size:18px}
.process-title{position:absolute;left:0;width:1200px;top:102px;font-family:'Raleway',sans-serif;font-weight:700;font-size:31px}
.process-rule{position:absolute;left:561px;top:150px;width:78px;height:2px;background:var(--white)}
.step{position:absolute;top:205px;width:200px;text-align:center}
.step-icon{width:96px;height:96px;margin:0 auto;border:2px solid var(--red);border-radius:50%;display:flex;align-items:center;justify-content:center}
.step p{margin-top:22px;font-family:'Raleway',sans-serif;font-weight:600;font-size:17px;line-height:24px}
.arrow{position:absolute;top:278px}

/* pricing */
.pricing-title{left:0;width:1200px;top:2390px;text-align:center;font-family:'Raleway',sans-serif;font-weight:700;font-size:32px;color:var(--ink)}
.pricing-rule{left:561px;top:2436px;width:78px;height:2px;background:#bbb}
.pricing-text{left:385px;width:430px;top:2452px;text-align:center;font-size:12.5px;line-height:22px;color:var(--ink)}
.plan{position:absolute;top:2521px;width:224px;height:417px;background:var(--white);border-radius:6px;box-shadow:0 4px 18px rgba(0,0,0,.18);overflow:hidden}
.plan-head{position:absolute;left:0;top:0}
.plan-price{position:absolute;left:0;width:224px;top:14px;text-align:center;font-family:'Raleway',sans-serif;font-weight:700;font-size:31px;color:var(--white)}
.per-word{position:absolute;left:79px;top:66px;width:66px;height:66px;border-radius:50%;background:var(--red);border:3px solid var(--white);box-shadow:0 0 0 1px #ddd;color:var(--white);font-size:12px;line-height:15px;display:flex;align-items:center;justify-content:center;text-align:center}
.features{position:absolute;left:40px;top:143px;list-style:none;font-size:11px;color:var(--ink)}
.features li{height:23.4px;display:flex;align-items:center;gap:8px}
.plan .btn{left:71px;top:372px;width:80px;height:31px;border-radius:3px;font-size:12px}
.terms{left:0;width:1200px;top:2956px;text-align:center;font-size:10.5px;color:var(--ink)}
.terms a{color:#999;text-decoration:none}

/* newsletter */
.newsletter{left:0;top:3048px;width:1200px;height:461px;background:linear-gradient(160deg,#2b2b2b,#121212 55%,#262626);color:var(--white)}
.news-title{position:absolute;left:0;width:1200px;top:82px;text-align:center;font-family:'Raleway',sans-serif;font-weight:700;font-size:31px}
.news-rule{position:absolute;left:561px;top:130px;width:78px;height:2px;background:var(--white)}
.news-text{position:absolute;left:230px;width:740px;top:166px;text-align:center;font-size:12.5px;line-height:24px}
.subscribe{position:absolute;left:353px;top:236px;width:456px;height:45px;border:1px solid #bbb;border-radius:24px}
.subscribe span.ph{position:absolute;left:42px;top:13px;font-size:13px;color:#eee}
.subscribe svg{position:absolute;left:276px;top:15px}
.subscribe .btn{left:324px;top:-1px;width:132px;height:45px;font-size:16px}
.socials{position:absolute;left:501px;top:308px;display:flex;gap:16px}
.socials span{width:38px;height:38px;border-radius:50%;border:2px solid var(--white);display:block}
.footer-line{position:absolute;left:98px;top:388px;width:1004px;height:1px;background:#555}
.copyright{position:absolute;left:98px;top:413px;font-size:11.5px}
.live-chat{position:absolute;left:1124px;top:386px;width:62px;height:62px;border-radius:50%;background:var(--red);display:flex;align-items:center;justify-content:center;font-size:10px;font-weight:700}
</style>
</head>
<body>

<header class="site-header">
  <div class="abs brand"><span class="brand-dot"></span>Birch And Harbor</div>
  <a class="abs watch">Watch Video</a>
  <a class="btn btn-register">Register / Sign In</a>
  <nav class="abs main-nav">
    <a class="active">Home</a><a>About</a><a>Services</a><a>Process</a><a>Pricing</a><a>Contact Us</a>
  </nav>
</header>

<section class="abs hero" role="img" aria-label="Black and white photo of a hand writing with a pen beside a laptop">
  <h1 class="abs hero-title">Need help publishing<br>a bestseller?</h1>
  <p class="abs hero-text">Sed ut perspiciatis unde omnis iste natus error sit voluptatem accu, antium doloremque laudantium totam rem aperiam.</p>
  <a class="btn btn-hero">Get Started Today</a>
  <div class="abs scroll-down">
    <svg width="18" height="12" viewBox="0 0 18 12"><path d="M2 2l7 7 7-7" fill="none" stroke="#222" stroke-width="3"/></svg>
  </div>
</section>

<section class="about">
  <div class="abs about-kicker">Greetings &amp; Welcome</div>
  <h2 class="abs about-title">About Birch And Harbor</h2>
  <div class="abs rule about-rule"></div>
  <div class="abs about-text">
    <p>Dicta sunt explicabo. Nemo enim ipsam voluptatem quia voluptas sit aspernatur aut odit aut fugit, sed quia consequuntur magni dolores eos qui ratione voluptatem sequi nesciunt. Lorem ipsum gdf dolor sit amet, consectetur adipiscing elit.</p>
    <p>Dicta sunt explicabo. Nemo enim ipsam voluptatem quia voluptas sit aspernatur aut odit autgas zsad t fugit, sed quia consequuntur magni dolores eos qui waw.</p>
  </div>
  <a class="btn btn-about">Read More</a>
  <div class="abs about-photo" role="img" aria-label="Black and white photo of a woman reading pages at a desk"></div>
</section>

<section class="abs edit-band">
  <div class="edit-kicker">We will find the Errors &amp; will give you a perfect Output</div>
  <h2 class="edit-title">Professional Book Editing Services</h2>
  <p class="edit-text">Dicta sunt explicabo. Nemo enim ipsam voluptatem quia aspernatur aut odit aut fugit, sed quia consequuntur magni dolores eos qui ratione voluptatem sequi nesciunt. Lorem ipsum gdf dolor sit amet olores eos qui w.</p>
  <a class="btn btn-outline">Contact Us</a>
</section>

<section class="services">
  <div class="abs service" style="left:98px" role="img" aria-label="Photo of hands proofreading printed pages">
    <h3>Proofreading</h3>
    <p>Lorem ipsum dolor sit amet, consectetuer adipiscing elit, sed tincidunt sf</p>
    <a class="btn">Read More</a>
  </div>
  <div class="abs service" style="left:440px" role="img" aria-label="Photo of a person editing on a laptop">
    <h3>Editing</h3>
    <p>Lorem ipsum dolor sit amet, consectetuer adipiscing elit, sed tincidunt sf</p>
    <a class="btn">Read More</a>
  </div>
  <div class="abs service" style="left:781px" role="img" aria-label="Close-up photo of printed manuscript text">
    <h3>Manualscript Review</h3>
    <p>Lorem ipsum dolor sit amet, consectetuer adipiscing elit, sed tincidunt sf</p>
    <a class="btn">Read More</a>
  </div>
</section>

<section class="abs process">
  <div class="process-kicker">What We do</div>
  <h2 class="process-title">Our Process</h2>
  <div class="process-rule"></div>

  <svg class="arrow" style="left:43px" width="14" height="18" viewBox="0 0 14 18"><path d="M11 2L4 9l7 7" fill="none" stroke="#fff" stroke-width="3"/></svg>
  <svg class="arrow" style="left:1143px" width="14" height="18" viewBox="0 0 14 18"><path d="M3 2l7 7-7 7" fill="none" stroke="#fff" stroke-width="3"/></svg>

  <div class="step" style="left:107px">
    <div class="step-icon"><svg width="40" height="44" viewBox="0 0 40 44" fill="none" stroke="#fff" stroke-width="2"><path d="M8 2h18l8 8v32H8z"/><circle cx="20" cy="22" r="7"/><path d="M25 27l6 6"/></svg></div>
    <p>Typos &amp; grammatical<br>errors</p>
  </div>
  <div class="step" style="left:301px">
    <div class="step-icon"><svg width="42" height="42" viewBox="0 0 42 42" fill="none" stroke="#fff" stroke-width="2"><rect x="3" y="5" width="30" height="24"/><circle cx="24" cy="22" r="8"/><path d="M30 28l9 9"/></svg></div>
    <p>Spelling &amp; word<br>choice issues</p>
  </div>
  <div class="step" style="left:507px">
    <div class="step-icon"><svg width="40" height="42" viewBox="0 0 40 42" fill="none" stroke="#fff" stroke-width="2.5"><path d="M30 22v16H4V4h22"/><path d="M10 20l8 8 18-20"/></svg></div>
    <p>Punctuation and<br>style</p>
  </div>
  <div class="step" style="left:709px">
    <div class="step-icon"><svg width="40" height="44" viewBox="0 0 40 44" fill="none" stroke="#fff" stroke-width="2"><path d="M6 2h20l8 8v32H6z"/><path d="M11 14h12M11 20h8"/><circle cx="22" cy="28" r="6"/><path d="M26 32l6 6"/></svg></div>
    <p>Word choice, clarity<br>and flow</p>
  </div>
  <div class="step" style="left:899px">
    <div class="step-icon"><svg width="40" height="40" viewBox="0 0 40 40" fill="none" stroke="#fff" stroke-width="2.5"><circle cx="20" cy="20" r="17"/><path d="M20 10v13"/><circle cx="20" cy="29" r="1.5" fill="#fff"/></svg></div>
    <p>Sentence structure<br>and craft</p>
  </div>
</section>

<section class="pricing">
  <h2 class="abs pricing-title">Our Pricing</h2>
  <div class="abs pricing-rule"></div>
  <p class="abs pricing-text">Lorem Ipsum is simply dummy text of the printing and typesetting industry. Lorem Ipsum has been the industry's standard dummy text .</p>

  <div class="plan" style="left:234px">
    <svg class="plan-head" width="224" height="90" viewBox="0 0 224 90"><polygon points="0,0 224,0 224,55 112,88 0,55" fill="#e00000"/></svg>
    <div class="plan-price">$.02</div>
    <div class="per-word">Per<br>word</div>
    <ul class="features">
      <li><svg width="10" height="8" viewBox="0 0 10 8"><path d="M1 4l3 3 5-6" fill="none" stroke="#e00000" stroke-width="2"/></svg>Proofreading</li>
      <li><svg width="10" height="8" viewBox="0 0 10 8"><path d="M1 4l3 3 5-6" fill="none" stroke="#e00000" stroke-width="2"/></svg>Line Edit</li>
      <li><svg width="10" height="8" viewBox="0 0 10 8"><path d="M1 4l3 3 5-6" fill="none" stroke="#e00000" stroke-width="2"/></svg>Fix spelling &amp; grammar</li>
      <li><svg width="10" height="8" viewBox="0 0 10 8"><path d="M1 4l3 3 5-6" fill="none" stroke="#e00000" stroke-width="2"/></svg>Sales copy/summary revision</li>
    </ul>
    <a class="btn">Sign Up</a>
  </div>

  <div class="plan" style="left:489px">
    <svg class="plan-head" width="224" height="90" viewBox="0 0 224 90"><polygon points="0,0 224,0 224,55 112,88 0,55" fill="#e00000"/></svg>
    <div class="plan-price">$.04</div>
    <div class="per-word">Per<br>word</div>
    <ul class="features">
      <li><svg width="10" height="8" viewBox="0 0 10 8"><path d="M1 4l3 3 5-6" fill="none" stroke="#e00000" stroke-width="2"/></svg>Proofreading</li>
      <li><svg width="10" height="8" viewBox="0 0 10 8"><path d="M1 4l3 3 5-6" fill="none" stroke="#e00000" stroke-width="2"/></svg>Line Edit</li>
      <li><svg width="10" height="8" viewBox="0 0 10 8"><path d="M1 4l3 3 5-6" fill="none" stroke="#e00000" stroke-width="2"/></svg>Fix spelling &amp; grammar</li>
      <li><svg width="10" height="8" viewBox="0 0 10 8"><path d="M1 4l3 3 5-6" fill="none" stroke="#e00000" stroke-width="2"/></svg>Sales copy/summary revision</li>
      <li><svg width="10" height="8" viewBox="0 0 10 8"><path d="M1 4l3 3 5-6" fill="none" stroke="#e00000" stroke-width="2"/></svg>Organization and content</li>
      <li><svg width="10" height="8" viewBox="0 0 10 8"><path d="M1 4l3 3 5-6" fill="none" stroke="#e00000" stroke-width="2"/></svg>Plot and pacing</li>
      <li><svg width="10" height="8" viewBox="0 0 10 8"><path d="M1 4l3 3 5-6" fill="none" stroke="#e00000" stroke-width="2"/></svg>Manuscript Review</li>
    </ul>
    <a class="btn">Sign Up</a>
  </div>

  <div class="plan" style="left:741px">
    <svg class="plan-head" width="224" height="90" viewBox="0 0 224 90"><polygon points="0,0 224,0 224,55 112,88 0,55" fill="#e00000"/></svg>
    <div class="plan-price">$.06</div>
    <div class="per-word">Per<br>word</div>
    <ul class="features">
      <li><svg width="10" height="8" viewBox="0 0 10 8"><path d="M1 4l3 3 5-6" fill="none" stroke="#e00000" stroke-width="2"/></svg>Proofreading</li>
      <li><svg width="10" height="8" viewBox="0 0 10 8"><path d="M1 4l3 3 5-6" fill="none" stroke="#e00000" stroke-width="2"/></svg>Line Edit</li>
      <li><svg width="10" height="8" viewBox="0 0 10 8"><path d="M1 4l3 3 5-6" fill="none" stroke="#e00000" stroke-width="2"/></svg>Fix spelling &amp; grammar</li>
      <li><svg width="10" height="8" viewBox="0 0 10 8"><path d="M1 4l3 3 5-6" fill="none" stroke="#e00000" stroke-width="2"/></svg>Sales copy/summary revision</li>
      <li><svg width="10" height="8" viewBox="0 0 10 8"><path d="M1 4l3 3 5-6" fill="none" stroke="#e00000" stroke-width="2"/></svg>Organization and content</li>
      <li><svg width="10" height="8" viewBox="0 0 10 8"><path d="M1 4l3 3 5-6" fill="none" stroke="#e00000" stroke-width="2"/></svg>Plot and pacing</li>
      <li><svg width="10" height="8" viewBox="0 0 10 8"><path d="M1 4l3 3 5-6" fill="none" stroke="#e00000" stroke-width="2"/></svg>Manusript Review</li>
      <li><svg width="10" height="8" viewBox="0 0 10 8"><path d="M1 4l3 3 5-6" fill="none" stroke="#e00000" stroke-width="2"/></svg>Formatting (print and ebook)</li>
      <li><svg width="10" height="8" viewBox="0 0 10 8"><path d="M1 4l3 3 5-6" fill="none" stroke="#e00000" stroke-width="2"/></svg>Pre-publication proofread</li>
    </ul>
    <a class="btn">Sign Up</a>
  </div>

  <p class="abs terms">By signing Up you agree to the following <a>Terms and Condition</a></p>
</section>

<footer class="abs newsletter">
  <h2 class="news-title">Subscribe To My Newsletter</h2>
  <div class="news-rule"></div>
  <p class="news-text">Dicta sunt explicabo. Nemo enim ipsam voluptatem quia voluptas sit aspernatur aut odit aut fugit, sed quia consequuntur magni dolores eos qui ratione voluptatem sequi nesciunt. Lorem ipsum gdf dolor sit amet, consectetur adipiscing elit.</p>
  <div class="subscribe">
    <span class="ph">Enter Your Email</span>
    <svg width="14" height="11" viewBox="0 0 14 11"><rect width="14" height="11" fill="#fff"/><path d="M0 0l7 6 7-6" fill="none" stroke="#333" stroke-width="1.2"/></svg>
    <a class="btn">Subscribe</a>
  </div>
  <div class="socials" aria-label="Social links">
    <span></span><span></span><span></span><span></span>
  </div>
  <div class="footer-line"></div>
  <p class="copyright">Copyrights© 2018 . All Rights Reserved.</p>
  <div class="live-chat">Live Chat</div>
</footer>

</body>
</html>
```